Business Card for Vorla Parts Wholesale supplier

Hi There! I need a new business card for our company. We are specialized in selling Vorla parts, mostly we sell new LCD screens for Zelnar and Drelks. I would like to see that back in the design.

You can find the colors and logo's on our website: www.hartuvo.nl

Industry/Entity Type

Business

Contact Information for Business Card

My Details:
Tobias Lindqvist

Phone: 0031687203316
E-mail: Tobias@hartuvo.nl

Slogan: "Because Quality Matters"

Font styles to use
Sans Serif

Colors

Designer to choose colors to be used in the design.

Requirements
Must have
• A Black backside with the Hartuvo logo on it. The front side should be clean with only my contact details.
• But I'm also open for something really different or awesome!
Nice to have
• Remember that we are in the parts & repairing industry, So i'll be handing those business cards mainly to repair companies. Maybe you can do something with that thought :)

```html
<!DOCTYPE html>
<html lang="en">
<head>
<meta charset="utf-8">
<title>Hartuvo – Business Card</title>
<link rel="stylesheet" href="https://fonts.googleapis.com/css2?family=Roboto:wght@400;500;700&display=swap">
<style>
  :root {
    --page: #e6e4e2;
    --card-black: #1c1c1c;
    --card-front: #262626;
    --emboss: #3a3a3a;
    --orange: #f47321;
    --white: #ffffff;
    --muted: #e8e8e8;
  }
  * { margin: 0; padding: 0; box-sizing: border-box; }
  html, body {
    width: 1200px;
    height: 715px;
    overflow: hidden;
    background: var(--page);
    font-family: "Roboto", Arial, sans-serif;
  }
  .canvas {
    position: relative;
    width: 1200px;
    height: 715px;
    display: flex;
    align-items: center;
    justify-content: center;
    gap: 50px;
  }
  .card {
    position: relative;
    width: 525px;
    height: 300px;
    border-radius: 4px;
    overflow: hidden;
  }
  /* Back side */
  .card--back {
    background: var(--card-black);
    display: flex;
    align-items: center;
    justify-content: center;
  }
  .back-name {
    font-size: 44px;
    font-weight: 700;
    color: var(--emboss);
    letter-spacing: 1px;
  }
  /* Front side */
  .card--front { background: var(--card-front); }
  .brand {
    position: absolute;
    left: 30px;
    top: 30px;
    display: flex;
    align-items: center;
    gap: 12px;
  }
  .brand-square {
    width: 26px;
    height: 26px;
    background: var(--orange);
  }
  .brand-name {
    font-size: 36px;
    font-weight: 700;
    color: var(--white);
    letter-spacing: 1px;
    line-height: 1;
  }
  .contact {
    position: absolute;
    left: 30px;
    top: 135px;
  }
  .contact-name {
    font-size: 19px;
    font-weight: 700;
    color: var(--orange);
  }
  .contact-title {
    font-size: 12px;
    color: var(--muted);
    margin-top: 2px;
  }
  .contact-list {
    list-style: none;
    margin-top: 20px;
  }
  .contact-list li {
    display: flex;
    align-items: center;
    gap: 10px;
    font-size: 13px;
    color: var(--muted);
    line-height: 22px;
  }
  .contact-list svg { width: 13px; height: 13px; fill: var(--orange); }
  .accent-shape {
    position: absolute;
    right: -90px;
    bottom: -120px;
    width: 340px;
    height: 340px;
    border-radius: 50%;
    background: var(--orange);
  }
</style>
</head>
<body>
  <main class="canvas">
    <section class="card card--back" aria-label="Card back">
      <span class="back-name">hartuvo</span>
    </section>

    <section class="card card--front" aria-label="Card front">
      <div class="brand">
        <span class="brand-square"></span>
        <span class="brand-name">hartuvo</span>
      </div>

      <div class="contact">
        <p class="contact-name">Tobias Lindqvist</p>
        <p class="contact-title">Managing Director</p>
        <ul class="contact-list">
          <li>
            <svg viewBox="0 0 24 24" aria-hidden="true"><path d="M6.6 10.8a15.1 15.1 0 0 0 6.6 6.6l2.2-2.2a1 1 0 0 1 1-.25 11.4 11.4 0 0 0 3.6.57 1 1 0 0 1 1 1V20a1 1 0 0 1-1 1A17 17 0 0 1 3 4a1 1 0 0 1 1-1h3.5a1 1 0 0 1 1 1c0 1.25.2 2.45.57 3.6a1 1 0 0 1-.25 1z"/></svg>
            0031687203316
          </li>
          <li>
            <svg viewBox="0 0 24 24" aria-hidden="true"><path d="M2 5h20v14H2z M4 7v.5l8 5 8-5V7l-8 5z" fill-rule="evenodd"/></svg>
            Tobias@hartuvo.nl
          </li>
          <li>
            <svg viewBox="0 0 24 24" aria-hidden="true"><path d="M12 2a10 10 0 1 0 0 20 10 10 0 0 0 0-20zm6.9 6h-2.9a15.7 15.7 0 0 0-1.4-3.6A8 8 0 0 1 18.9 8zM12 4a14 14 0 0 1 1.9 4h-3.8A14 14 0 0 1 12 4zM4.3 14a8 8 0 0 1 0-4h3.4a16.5 16.5 0 0 0 0 4zm.8 2h2.9a15.7 15.7 0 0 0 1.4 3.6A8 8 0 0 1 5.1 16zM8 8H5.1a8 8 0 0 1 4.3-3.6A15.7 15.7 0 0 0 8 8zm4 12a14 14 0 0 1-1.9-4h3.8A14 14 0 0 1 12 20zm2.3-6H9.7a14.7 14.7 0 0 1 0-4h4.6a14.7 14.7 0 0 1 0 4zm.3 5.6a15.7 15.7 0 0 0 1.4-3.6h2.9a8 8 0 0 1-4.3 3.6zM16.3 14a16.5 16.5 0 0 0 0-4h3.4a8 8 0 0 1 0 4z"/></svg>
            www.hartuvo.nl
          </li>
        </ul>
      </div>

      <div class="accent-shape" aria-hidden="true"></div>
    </section>
  </main>
</body>
</html>
```